New Wrestling company needs a website

We need a website design for a new wrestling company in Australia that will be running 3-4 events per year. Wrestling company is Summit Grip Wrestling (SGW).

The design of the logo is in place and can be provided, and I have purchased the website domain.

A detailed description of the intent and purpose of this company can be provided.

The aim would be to have around 5 specific pages on SGW, with two standard “about” and “contact” pages. E.g.
- About SGW (focus and purpose of the company)
- SGW Events (specific focus on events run by SGW)
- SGW News (news and stories on wrestling’s across Oceania)
- SGW Media (where to watch SGW and our partners))
- SGW Partners and Sponsors (partner and affiliate information)
- SGW Power Rankings (top 10 ranked wrestlers from Oceania which is updated weekly)
- SGW fans (highlighting how to become part of SGW as a fan)
- Contact SGW
Updates

The logo design should now be included in the brief, please feel free to reach out to me directly if you can't access it or require any other information.

Target Market(s)

Wrestling Fans

Industry/Entity Type

Sport / Wrestling

Coding

Coded - Design and coding required

Number of Pages Required

5+ page

Requirements
Must have
• A Wrestling and or Sports feel to the website design

```html
<!DOCTYPE html>
<html lang="en">
<head>
<meta charset="utf-8">
<title>Summit Grip Wrestling</title>
<link href="https://fonts.googleapis.com/css2?family=Raleway:wght@600;700;800&family=Lato:wght@400;700&display=swap" rel="stylesheet">
<style>
:root{
  --black:#000;
  --panel:#121212;
  --footer:#0e0e0e;
  --row:#151515;
  --blue:#2a9be0;
  --blue-deep:#1f5fae;
  --blue-btn:#1d7fcf;
  --white:#fff;
  --grey:#2b2b2b;
  --head:"Raleway",sans-serif;
  --body:"Lato",sans-serif;
}
*{box-sizing:border-box;margin:0;padding:0}
html,body{width:1200px;height:4270px;overflow:hidden;background:var(--black);color:var(--white);font-family:var(--body)}
.page{position:relative;width:1200px;height:4270px;overflow:hidden}
.abs{position:absolute}
.brand{font-family:var(--head);font-weight:800;font-size:40px;line-height:48px;color:var(--blue);letter-spacing:1px}
.btn{display:flex;align-items:center;justify-content:center;background:linear-gradient(90deg,var(--blue-btn),var(--blue));border-radius:30px;font-family:var(--head);font-weight:700;color:var(--white);font-size:15px}
h2.section-title{font-family:var(--head);font-weight:700;font-size:34px;line-height:40px}
.lede{font-size:16px;line-height:31px;color:var(--white)}

.topbar{left:0;top:0;width:1200px;height:96px;background:var(--black)}
.icon-dot{width:34px;height:34px;border-radius:50%;background:var(--blue);display:flex;align-items:center;justify-content:center}
.contact-small{font-size:14px;color:var(--white)}
.contact-big{font-size:19px;font-weight:700;color:var(--white)}
.nav{left:0;top:96px;width:1200px;height:53px;background:linear-gradient(90deg,#2a8fd8,#2ea6ea);display:flex;align-items:center;justify-content:space-between;padding:0 135px}
.nav a{color:var(--white);font-size:15px;text-decoration:none}

.hero{left:0;top:149px;width:1200px;height:638px;background:
 radial-gradient(ellipse 380px 300px at 240px 120px,rgba(60,170,255,.75),transparent 70%),
 radial-gradient(ellipse 360px 260px at 930px 260px,rgba(230,20,50,.85),transparent 70%),
 linear-gradient(90deg,#06162a,#0c0d18 50%,#2a0610)}
.hero-title{left:300px;top:248px;width:566px;text-align:center;font-family:var(--head);font-weight:700;font-size:44px;line-height:50px}
.hero-text{left:350px;top:365px;width:466px;text-align:center;font-size:15px;line-height:27px}
.dots{left:552px;top:572px;display:flex;gap:4px}
.dots span{width:10px;height:10px;border-radius:50%;background:var(--white)}
.dots span.off{background:transparent;border:1.5px solid var(--white)}

.about{left:0;top:787px;width:1200px;height:582px;background:var(--panel)}
.ring{left:111px;top:70px;width:442px;height:442px;border-radius:50%;background:linear-gradient(135deg,#1f5fae,#2a9be0)}
.ring-photo{left:128px;top:88px;width:400px;height:400px;border-radius:50%;background:linear-gradient(160deg,#d9dde0,#7a97b8 55%,#2f5fa8)}
.about-title{left:616px;top:90px;font-family:var(--head);font-weight:700;font-size:34px;line-height:40px}
.about-text{left:616px;top:143px;width:476px;font-size:15px;line-height:25.7px;color:var(--white)}

.events{left:0;top:1369px;width:1200px;height:659px;background:var(--black)}
.card{top:271px;width:316px;height:203px}
.card-feature{background:linear-gradient(135deg,#1f63b8,#2b8fd8);text-align:center;padding-top:40px}
.card-feature h3{font-family:var(--head);font-weight:700;font-size:19px;margin-bottom:10px}
.card-feature p{font-size:16px;line-height:26px}
.card-feature a{display:inline-block;margin-top:8px;color:var(--white);font-size:14px;font-weight:700;text-decoration:underline}
.track{left:111px;top:565px;width:978px;height:5px;background:var(--grey)}
.track span{position:absolute;left:0;top:0;width:175px;height:5px;background:var(--blue)}

.media{left:0;top:2028px;width:1200px;height:806px;background:linear-gradient(180deg,#245aa5,#2a8ccb)}
.frame{width:318px;height:212px;background:var(--white);padding:7px}
.frame div{width:100%;height:100%}

.rankings{left:0;top:2834px;width:1200px;height:944px;background:var(--black)}
.centre-title{width:1200px;text-align:center}
.rank-head{font-family:var(--head);font-weight:700;font-size:17px}
.rank-row{width:424px;height:75px;background:var(--row);border-radius:8px;overflow:hidden;display:flex;align-items:center}
.rank-photo{width:88px;height:75px;flex:none}
.rank-name{font-family:var(--head);font-weight:700;font-size:18px;width:296px;padding-left:22px}
.rank-num{font-family:var(--head);font-weight:700;font-size:18px}
.partner{top:783px;width:202px;height:77px;background:#1c1c1c;display:flex;align-items:center;justify-content:center}
.partner span{width:54px;height:54px;border-radius:50%;background:#3a3a3a}

.footer-bg{left:0;top:3770px;width:1200px;height:500px}
.foot-title{font-family:var(--head);font-weight:700;font-size:21px}
.foot-list{list-style:none;font-size:15px;line-height:30px}
.foot-text{font-size:15px;line-height:26px}
.news-input{left:827px;top:3987px;width:258px;height:35px;border:1px solid #3a6fa8;border-radius:6px;font-size:13px;color:#777;padding:9px 12px}
.socials{left:836px;top:4056px;display:flex;gap:12px}
.socials span{width:13px;height:13px;border-radius:50%;background:var(--white)}
.copy{left:0;top:4246px;width:1200px;text-align:center;font-size:15px}
</style>
</head>
<body>
<div class="page">

  <header class="abs topbar">
    <div class="abs brand" style="left:116px;top:20px">SGW</div>
    <div class="abs icon-dot" style="left:452px;top:21px">
      <svg width="16" height="16" viewBox="0 0 24 24"><path fill="#fff" d="M6.6 10.8a15 15 0 0 0 6.6 6.6l2.2-2.2a1 1 0 0 1 1-.25 11.4 11.4 0 0 0 3.6.57 1 1 0 0 1 1 1V20a1 1 0 0 1-1 1A17 17 0 0 1 3 4a1 1 0 0 1 1-1h3.5a1 1 0 0 1 1 1c0 1.25.2 2.45.57 3.57a1 1 0 0 1-.25 1z"/></svg>
    </div>
    <div class="abs contact-small" style="left:499px;top:20px">Call Us Free</div>
    <div class="abs contact-big" style="left:499px;top:42px">+ 1-800-555-0142</div>
    <div class="abs icon-dot" style="left:692px;top:21px">
      <svg width="14" height="18" viewBox="0 0 24 30"><path fill="#fff" d="M12 0a9 9 0 0 0-9 9c0 7 9 21 9 21s9-14 9-21a9 9 0 0 0-9-9zm0 12a3 3 0 1 1 0-6 3 3 0 0 1 0 6z"/></svg>
    </div>
    <div class="abs contact-small" style="left:742px;top:22px;width:210px;line-height:26px">Lorem ipsum dolor sit amet consectetur</div>
    <div class="abs btn" style="left:983px;top:18px;width:104px;height:45px;font-size:16px">
      <svg width="12" height="13" viewBox="0 0 12 13" style="margin-right:8px"><circle cx="6" cy="3.5" r="3" fill="#fff"/><path d="M0 13a6 5 0 0 1 12 0z" fill="#fff"/></svg>Login
    </div>
  </header>
  <nav class="abs nav">
    <a>About SGW</a><a>SGW Events</a><a>SGW News</a><a>SGW Partners</a><a>SGW Power Rankings</a><a>SGW fans</a><a>SGW Contact</a>
  </nav>

  <section class="abs hero" role="img" aria-label="Wrestling ring lit in blue and red stage light">
    <h1 class="abs hero-title">Welcome To Summit Grip Wrestling</h1>
    <p class="abs hero-text">Lorem ipsum dolor sit amet, consectetur adipiscing elit, sed do eiusmod tempor incididunt ut labore</p>
    <div class="abs btn" style="left:506px;top:438px;width:149px;height:56px">Get Started</div>
    <div class="abs dots"><span></span><span></span><span class="off"></span><span></span><span></span></div>
    <svg class="abs" style="left:0;top:0" width="1200" height="638" viewBox="0 0 1200 638">
      <path d="M0 548 C250 600 500 640 650 640 L0 640Z" fill="#121212"/>
      <path d="M620 640 C850 600 1000 560 1200 458 L1200 475 C1020 575 860 620 700 640Z" fill="#2a9be0"/>
      <path d="M640 640 C860 610 1020 570 1200 478 L1200 640Z" fill="#121212"/>
    </svg>
  </section>

  <section class="abs about">
    <div class="abs ring"></div>
    <div class="abs ring-photo" role="img" aria-label="Wrestler lifting an opponent in a gym"></div>
    <h2 class="abs about-title">About Summit Grip Wrestling</h2>
    <p class="abs about-text">Lorem ipsum dolor sit amet, consectetur adipiscing elit, sed do eiusmod tempor incididunt ut labore et dolore magna aliqua. Ut enim ad minim veniam, quis nostrud exercitation ullamco laboris nisi ut aliquip ex ea commodo consequat. Duis aute irure dolor in reprehenderit in voluptate velit esse cillum dolore eu fugiat nulla pariatur.Lorem ipsum dolor sit amet, consectetur adipiscing elit, sed do eiusmod tempor incididunt ut labore et dolore magna aliqua. Ut enim ad minim veniam, quis nostrud exercitation ullamco laboris nisi ut aliquip ex ea commodo consequat. Duis aute irure dolor in reprehenderit in voluptate velit esse cillum</p>
    <div class="abs btn" style="left:616px;top:424px;width:148px;height:57px">Learn More</div>
  </section>

  <section class="abs events">
    <h2 class="abs section-title" style="left:111px;top:76px">Our Events</h2>
    <p class="abs lede" style="left:118px;top:136px;width:745px">Lorem ipsum dolor sit amet, consectetur adipiscing elit, sed do eiusmod tempor incididunt ut labore et dolore magna aliqua. Quis ipsum suspendisse ultrices gravida. Risus commodo viverra maecenas accumsan lacus vel facilisis.</p>
    <div class="abs card" style="left:111px;background:linear-gradient(160deg,#c9c3b4,#8a3a3a 60%,#c23030)" role="img" aria-label="Two wrestlers grappling on a red mat"></div>
    <div class="abs card card-feature" style="left:441px">
      <h3>Lorem ipsum</h3>
      <p>Lorem ipsum dolor sit amet,<br>consectetur adipiscing</p>
      <a>Learn More</a>
    </div>
    <div class="abs card" style="left:771px;background:linear-gradient(160deg,#4a4a4a,#2a2a2a 55%,#5a5040)" role="img" aria-label="Wrestlers in headgear locked together"></div>
    <div class="abs track"><span></span></div>
  </section>

  <section class="abs media">
    <h2 class="abs section-title" style="left:110px;top:83px">Our Media</h2>
    <p class="abs lede" style="left:112px;top:138px;width:745px">Lorem ipsum dolor sit amet, consectetur adipiscing elit, sed do eiusmod tempor incididunt ut labore et dolore magna aliqua. Quis ipsum suspendisse ultrices gravida. Risus commodo viverra maecenas accumsan lacus vel facilisis.</p>
    <div class="abs frame" style="left:109px;top:270px"><div role="img" aria-label="Wrestlers on a dark backdrop" style="background:linear-gradient(135deg,#0c0f1e,#7a2a2a 60%,#1a2a5a)"></div></div>
    <div class="abs frame" style="left:441px;top:270px"><div role="img" aria-label="Two wrestlers under spotlights" style="background:radial-gradient(circle at 50% 40%,#8a7fa0,#2a2a30 70%)"></div></div>
    <div class="abs frame" style="left:772px;top:270px"><div role="img" aria-label="Wrestling match in a sports hall" style="background:linear-gradient(160deg,#b8a89a,#c9423a 55%,#8a8a8a)"></div></div>
    <div class="abs frame" style="left:109px;top:504px"><div role="img" aria-label="Wrestlers on a white and red mat" style="background:linear-gradient(160deg,#6a6a6a,#c84a4a 50%,#e0dcd8)"></div></div>
    <div class="abs frame" style="left:441px;top:504px"><div role="img" aria-label="Wrestlers on a red mat" style="background:linear-gradient(160deg,#1a1a1a,#b8242a 60%,#2a3a80)"></div></div>
    <div class="abs frame" style="left:772px;top:504px"><div role="img" aria-label="Crowded wrestling bout" style="background:linear-gradient(160deg,#6a5a4a,#b88a5a 50%,#3a3a2a)"></div></div>
  </section>

  <section class="abs rankings">
    <h2 class="abs section-title centre-title" style="left:-5px;top:62px">Power Rankings</h2>
    <div class="abs rank-head" style="left:512px;top:138px">Rank</div>
    <div class="abs rank-head" style="left:964px;top:138px">Rank</div>

    <div class="abs rank-row" style="left:147px;top:167px"><div class="rank-photo" role="img" aria-label="Wrestler portrait" style="background:linear-gradient(135deg,#6a4a2a,#2a2a2a)"></div><div class="rank-name">Addison Alexander</div><div class="rank-num">1</div></div>
    <div class="abs rank-row" style="left:147px;top:261px"><div class="rank-photo" role="img" aria-label="Wrestler portrait" style="background:linear-gradient(135deg,#3a3a3a,#6a2a2a)"></div><div class="rank-name">Adaline Becka</div><div class="rank-num">2</div></div>
    <div class="abs rank-row" style="left:147px;top:357px"><div class="rank-photo" role="img" aria-label="Wrestler portrait" style="background:linear-gradient(135deg,#2a2a2a,#8a2a3a)"></div><div class="rank-name">Andrew Bert</div><div class="rank-num">3</div></div>
    <div class="abs rank-row" style="left:147px;top:452px"><div class="rank-photo" role="img" aria-label="Wrestler portrait" style="background:linear-gradient(135deg,#9a9a9a,#4a4a4a)"></div><div class="rank-name">Orana Taleebin</div><div class="rank-num">4</div></div>
    <div class="abs rank-row" style="left:147px;top:546px"><div class="rank-photo" role="img" aria-label="Wrestler portrait" style="background:linear-gradient(135deg,#1a1a1a,#7a4a3a)"></div><div class="rank-name">John Doe</div><div class="rank-num">5</div></div>

    <div class="abs rank-row" style="left:598px;top:167px"><div class="rank-photo" role="img" aria-label="Wrestler portrait" style="background:linear-gradient(135deg,#1a2a4a,#3a5a8a)"></div><div class="rank-name">Addison Alexander</div><div class="rank-num">6</div></div>
    <div class="abs rank-row" style="left:598px;top:261px"><div class="rank-photo" role="img" aria-label="Wrestler portrait" style="background:linear-gradient(135deg,#1a1a1a,#5a2a2a)"></div><div class="rank-name">Adaline Becka</div><div class="rank-num">7</div></div>
    <div class="abs rank-row" style="left:598px;top:357px"><div class="rank-photo" role="img" aria-label="Wrestler portrait" style="background:linear-gradient(135deg,#2a2a2a,#8a2a3a)"></div><div class="rank-name">Andrew Bert</div><div class="rank-num">8</div></div>
    <div class="abs rank-row" style="left:598px;top:452px"><div class="rank-photo" role="img" aria-label="Wrestler portrait" style="background:linear-gradient(135deg,#1a1a1a,#4a3a3a)"></div><div class="rank-name">Orana Taleebin</div><div class="rank-num">9</div></div>
    <div class="abs rank-row" style="left:598px;top:546px"><div class="rank-photo" role="img" aria-label="Wrestler portrait" style="background:linear-gradient(135deg,#2a3a8a,#c8304a)"></div><div class="rank-name">John Doe</div><div class="rank-num">10</div></div>

    <h2 class="abs section-title centre-title" style="left:-5px;top:698px">Our Partners</h2>
    <svg class="abs" style="left:50px;top:815px" width="12" height="14" viewBox="0 0 12 14"><path d="M8 2 3 7l5 5" stroke="#aaa" stroke-width="1.6" fill="none"/></svg>
    <svg class="abs" style="left:1138px;top:815px" width="12" height="14" viewBox="0 0 12 14"><path d="M4 2l5 5-5 5" stroke="#aaa" stroke-width="1.6" fill="none"/></svg>
    <div class="abs partner" style="left:141px"><span></span></div>
    <div class="abs partner" style="left:378px"><span></span></div>
    <div class="abs partner" style="left:613px"><span></span></div>
    <div class="abs partner" style="left:850px"><span></span></div>
  </section>

  <footer>
    <svg class="abs footer-bg" width="1200" height="500" viewBox="0 0 1200 500">
      <rect width="1200" height="500" fill="#000"/>
      <path d="M0 200 C150 120 300 40 480 10 C700 -10 950 20 1200 70 L1200 500 L0 500Z" fill="#0e0e0e"/>
      <path d="M0 195 C120 110 280 30 470 12 L420 18 C260 50 120 120 0 215Z" fill="#2a9be0"/>
    </svg>
    <div class="abs brand" style="left:126px;top:3972px">SGW</div>
    <p class="abs foot-text" style="left:121px;top:4060px;width:260px">Lorem ipsum dolor sit amet, consectetur adipiscing elit, sed do eiusmod tempor incididunt ut labore et dolore magna aliqua.</p>

    <h3 class="abs foot-title" style="left:428px;top:3940px">Quick Link</h3>
    <ul class="abs foot-list" style="left:432px;top:3980px">
      <li>About SGW</li><li>SGW Events</li><li>SGW News</li><li>SGW Partners</li><li>SGW Power Rankings</li><li>SGW fans</li><li>SGW Contact</li>
    </ul>
    <h3 class="abs foot-title" style="left:618px;top:3940px">Help Link</h3>
    <ul class="abs foot-list" style="left:624px;top:3980px">
      <li>Terms&amp;condtions</li><li>Privacy Policy</li><li>About Us</li><li>Support</li>
    </ul>
    <h3 class="abs foot-title" style="left:825px;top:3940px">Get Our Newsletter</h3>
    <div class="abs news-input">Enter Your Email</div>
    <svg class="abs" style="left:1058px;top:3996px" width="16" height="16" viewBox="0 0 24 24"><path d="M2 12 22 3l-6 19-4-8z" fill="#2a9be0"/></svg>
    <div class="abs socials"><span></span><span></span><span></span><span></span></div>

    <div class="abs copy">©Copyrights 2022 Summit Grip Wrestling &nbsp;|&nbsp;&nbsp; All Rights Reserved</div>
  </footer>

</div>
</body>
</html>
```